Web design for Crowdfunding site HopeWingsRally.com

We need a web design for christian crowdfunding website. Here is the challenge: We need responsive layout that is targeted first in iPad size of screen. It should also scale somehow down to iPhone size of screens. Web layout can be about the same size as iPad screen.

Screens should work so that main page scrolls not but only certain part of the screen scrolls and always one "page" at time. We can implement these "scrolls" then later with javascript but now we need only design. The challenge is to create this kind of hybrid website / app look.

Target is at first to raise funds to orphan people needing about $40 per month for their living and education. There is always some organization which takes care of these kids. Later there will be other christian missions included. At first we are looking to find monthly supporters.

You can be as creative as you want :) As you see from the look and feel sector, I am not looking any same traditional look which many "help kids" sites have. I am looking to reach now younger generation and therefore iPad and mobile are the main screen sizes.

Inspirational designs:
- https://example-gallery.test/profiles/studiofernlake/designs/482716?from=%2Fbrowse%2Fxhr%2Fdesigns%3Fcategory%3Dmobile-app-design
- http://www.artpoolhub.test/design/8261047 Clear, simple visuals
- http://www.artpoolhub.test/design/7394215 Header
- http://www.artpoolhub.test/design/6048392 Contrast in the colors, i think is powerfull

Some terms could be: Kids play, kids are learning (in the school). No static posture but living like kids are. I wonder also how we could also add little bit gaming style even though the question is of reali life of real people. Giving should be rewarding.

Target Market(s)

People who want help other people.

Industry/Entity Type

Christian

Number of Pages Required

4 page

Requirements
Must have
• Homepage. Mission page (In my wireframes it was one kid).
Nice to have
• Other pages and some idea how to scroll. 4 pages is no must. If you feel easy, please give first some draft and I give comments on that.

```html
<!DOCTYPE html>
<html lang="en">
<head>
<meta charset="utf-8">
<title>HopeWingsRally – Monthly Supporters</title>
<link rel="stylesheet" href="https://fonts.googleapis.com/css2?family=Roboto+Slab:wght@300;400;700&family=Roboto:wght@400&display=swap">
<style>
  :root {
    --brand-orange: #ffad00;
    --panel-white: #ffffff;
    --header-grey: #f5f5f5;
    --ink-dark: #474747;
    --nav-text: #555555;
    --arrow-blue: #2f5a8a;
    --footer-text: #ffffff;
  }
  * { box-sizing: border-box; margin: 0; padding: 0; }
  html, body {
    width: 1200px;
    height: 860px;
    overflow: hidden;
  }
  body {
    position: relative;
    background: var(--brand-orange);
    font-family: "Roboto Slab", Georgia, serif;
  }
  .site-panel {
    position: absolute;
    left: 99px;
    top: 63px;
    width: 1005px;
    height: 700px;
    background: var(--panel-white);
  }
  .site-header {
    position: relative;
    height: 67px;
    background: var(--header-grey);
    color: var(--nav-text);
    font-size: 13px;
    text-transform: uppercase;
  }
  .nav-left, .nav-right {
    position: absolute;
    top: 0;
    height: 67px;
    display: flex;
    align-items: center;
  }
  .nav-left { left: 48px; gap: 6px; }
  .nav-right { right: 46px; gap: 24px; }
  .nav-link { display: flex; align-items: center; gap: 6px; color: var(--nav-text); text-decoration: none; }
  .nav-search { margin-left: 10px; display: flex; }
  .brand-name {
    position: absolute;
    left: 0; right: 0; top: 0;
    height: 67px;
    line-height: 67px;
    text-align: center;
    font-weight: 700;
    font-size: 22px;
    color: var(--ink-dark);
    letter-spacing: 0.2px;
  }
  .mission-pitch {
    position: absolute;
    left: 0; right: 0;
    top: 154px;
    text-align: center;
    font-weight: 300;
    font-size: 27px;
    line-height: 34px;
    color: var(--brand-orange);
  }
  .supporter-chain {
    position: absolute;
    left: 0; top: 0;
    width: 1005px;
    height: 700px;
  }
  .site-footer {
    position: absolute;
    left: 0; right: 0;
    top: 801px;
    text-align: center;
    font-family: "Roboto", Arial, sans-serif;
    font-size: 13px;
    color: var(--footer-text);
  }
</style>
</head>
<body>
  <svg width="0" height="0" style="position:absolute">
    <defs>
      <symbol id="person" viewBox="-20 -22 40 44">
        <circle cx="0" cy="-10" r="9" fill="#fff"/>
        <path d="M-17 21 V8 Q-17 1 -9 1 H9 Q17 1 17 8 V21 Z" fill="#fff"/>
      </symbol>
      <marker id="arrow-tip" viewBox="0 0 10 10" refX="6" refY="5" markerWidth="4.2" markerHeight="4.2" orient="auto">
        <path d="M0 0 L10 5 L0 10 Z" fill="var(--arrow-blue)"/>
      </marker>
    </defs>
  </svg>

  <main class="site-panel">
    <header class="site-header">
      <nav class="nav-left">
        <a class="nav-link" href="#missions">
          <svg width="13" height="11" viewBox="0 0 13 11" aria-hidden="true">
            <g fill="var(--nav-text)">
              <rect x="0" y="0" width="2.5" height="2"/><rect x="3.5" y="0" width="9.5" height="2"/>
              <rect x="0" y="3" width="2.5" height="2"/><rect x="3.5" y="3" width="9.5" height="2"/>
              <rect x="0" y="6" width="2.5" height="2"/><rect x="3.5" y="6" width="9.5" height="2"/>
              <rect x="0" y="9" width="2.5" height="2"/><rect x="3.5" y="9" width="9.5" height="2"/>
            </g>
          </svg>
          See the missions
        </a>
        <span class="nav-search" aria-label="Search">
          <svg width="12" height="12" viewBox="0 0 12 12" aria-hidden="true">
            <circle cx="5" cy="5" r="3.6" fill="none" stroke="var(--nav-text)" stroke-width="2"/>
            <line x1="7.7" y1="7.7" x2="11" y2="11" stroke="var(--nav-text)" stroke-width="2.2" stroke-linecap="round"/>
          </svg>
        </span>
      </nav>
      <div class="brand-name">HOPEWINGSRALLY</div>
      <nav class="nav-right">
        <a class="nav-link" href="#login">
          <svg width="11" height="12" viewBox="0 0 11 12" aria-hidden="true">
            <circle cx="5.5" cy="3" r="3" fill="var(--nav-text)"/>
            <path d="M0 12 V9 Q0 6.5 2.5 6.5 H8.5 Q11 6.5 11 9 V12 Z" fill="var(--nav-text)"/>
          </svg>
          Log in
        </a>
        <a class="nav-link" href="#signup">Sign up</a>
      </nav>
    </header>

    <p class="mission-pitch">
      She has a name.He has Dreams.She hopes she would have a future.<br>
      He is'Like You, I USD a month will help her and him
    </p>

    <svg class="supporter-chain" viewBox="0 0 1005 700" aria-label="Chain of supporters, each passing help on to the next">
      <g fill="var(--ink-dark)">
        <circle cx="157" cy="401" r="51"/>
        <circle cx="329" cy="401" r="51"/>
        <circle cx="501" cy="401" r="51" fill="var(--brand-orange)"/>
        <circle cx="672" cy="401" r="51"/>
        <circle cx="844" cy="401" r="51"/>
        <circle cx="244" cy="574" r="51"/>
        <circle cx="415" cy="574" r="51"/>
        <circle cx="588" cy="574" r="51"/>
        <circle cx="759" cy="574" r="51"/>
      </g>
      <g>
        <use href="#person" x="139" y="382" width="36" height="40"/>
        <use href="#person" x="311" y="382" width="36" height="40"/>
        <use href="#person" x="483" y="382" width="36" height="40"/>
        <use href="#person" x="654" y="382" width="36" height="40"/>
        <use href="#person" x="826" y="382" width="36" height="40"/>
        <use href="#person" x="226" y="555" width="36" height="40"/>
        <use href="#person" x="397" y="555" width="36" height="40"/>
        <use href="#person" x="570" y="555" width="36" height="40"/>
        <use href="#person" x="741" y="555" width="36" height="40"/>
      </g>
      <g fill="none" stroke="var(--arrow-blue)" stroke-width="3" stroke-linecap="round" marker-end="url(#arrow-tip)">
        <path d="M214 395 Q236 416 259 394"/>
        <path d="M386 408 Q409 382 430 405"/>
        <path d="M558 395 Q580 416 603 394"/>
        <path d="M730 408 Q753 382 774 405"/>
        <path d="M301 568 Q323 589 346 567"/>
        <path d="M472 581 Q495 555 516 578"/>
        <path d="M645 568 Q667 589 690 567"/>
      </g>
    </svg>
  </main>

  <footer class="site-footer">Copyright © 2016&nbsp; All Rights Reserved</footer>
</body>
</html>
```